Bramwell Lodge Business Cards design with a logo

I want two Business cards designed with a very modern contemporary logo UNING 1920'S FONT STYLES with the following details

Address:
Bramwell Lodge
17 Pellham Road
Kilbrannan
G83 2RN

Details for card 1

Name: Dermot Ashby
email: Dermot.ashby@bramwell.lodge
Tel : +971 52 318 6094
Tel +44 7700 900 318

Details Card 2

Name: Dermot Ashby
email: Neville.osgood@bramwell.lodge
Tel : +971 52 430 9187

Bramwell lodge is a house that was built around 1880 and was used extensively in the 1920's for entertaining and parties in the arts scene, the house again will be resurrected to a modern entertainment venue

If you have any questions feel free to ask

Target Market(s)

The market for this is the young modern crowd

Industry/Entity Type

Entertainment Industry

Contact Information for Business Card

Address:
Bramwell Lodge
17 Pellham Road
Kilbrannan
G83 2RN

Details for card 1

Name: Dermot Ashby
Tel : +971 52 318 6094
Tel +44 7700 900 318

Details Card 2

Name: Neville Osgood
Tel : +971 52 430 9187

Logo Text

Bramwell Lodge

Font styles to use
Other font styles liked:
• 1920'S FONT STULES

Requirements
Must have
• Modern Contemporary, whilst taking into consideration the age of the house as detailed above. YOU MUT BE USING 1920'S FONT STYLES
Nice to have
• 1920'S FONT STYLES see attached image if a suggestion
Should not have
• Should not look old or dated

```html
<!DOCTYPE html>
<html lang="en">
<head>
<meta charset="utf-8">
<title>Bramwell Lodge – Business Cards</title>
<link rel="stylesheet" href="https://fonts.googleapis.com/css2?family=Montserrat:wght@500;600&family=Work+Sans:wght@400;500&display=swap">
<style>
  :root {
    --backdrop: #1d1d1e;
    --card: #232324;
    --card-edge: #2c2c2d;
    --ink: #f2f2f2;
    --ink-soft: #d9d9d9;
    --accent: #ffe100;
  }
  * { box-sizing: border-box; margin: 0; padding: 0; }
  html, body {
    width: 1200px; height: 900px; overflow: hidden;
    background: var(--backdrop);
  }
  .canvas {
    position: relative; width: 1200px; height: 900px;
    display: flex; flex-direction: column; align-items: center; justify-content: center; gap: 40px;
  }
  .card {
    position: relative; width: 660px; height: 377px;
    background: linear-gradient(160deg, var(--card-edge) 0%, var(--card) 55%, #1f1f20 100%);
    border-bottom: 4px solid var(--accent);
    box-shadow: 0 18px 40px rgba(0,0,0,.45);
    overflow: hidden;
  }
  .wordmark {
    font-family: "Montserrat", sans-serif;
    font-weight: 500;
    color: var(--ink);
    letter-spacing: .5px;
    white-space: nowrap;
  }
  /* Front */
  .card--front .wordmark {
    position: absolute; left: 0; right: 0; top: 138px;
    text-align: center; font-size: 52px;
  }
  .card--front .web {
    position: absolute; left: 0; right: 0; bottom: 34px;
    text-align: center;
    font-family: "Work Sans", sans-serif; font-size: 15px; letter-spacing: .6px;
    color: var(--ink-soft);
  }
  .domain { color: var(--accent); }
  /* Back */
  .card--back .wordmark {
    position: absolute; left: 38px; top: 152px; font-size: 30px;
  }
  .divider {
    position: absolute; left: 330px; top: 78px; width: 2px; height: 192px;
    background: var(--accent);
  }
  .contact {
    position: absolute; left: 354px; top: 74px;
    font-family: "Work Sans", sans-serif; color: var(--ink); font-size: 16px; letter-spacing: .8px;
  }
  .contact .person {
    font-family: "Montserrat", sans-serif; font-weight: 600;
    color: var(--accent); font-size: 24px; letter-spacing: .3px; line-height: 1.1;
  }
  .contact .role { font-size: 15px; color: var(--ink-soft); margin-bottom: 14px; }
  .contact .address { line-height: 1.4; margin-bottom: 12px; }
  .contact ul { list-style: none; }
  .contact li { display: flex; align-items: center; gap: 10px; line-height: 1.55; white-space: nowrap; }
  .contact li svg { width: 11px; height: 11px; flex: none; }
  .contact li svg * { fill: none; stroke: var(--accent); stroke-width: 1.6; }
</style>
</head>
<body>
<main class="canvas">

  <section class="card card--front" aria-label="Card front">
    <div class="wordmark">Bramwell Lodge</div>
    <div class="web">www.<span class="domain">bramwelllodge</span>.com</div>
  </section>

  <section class="card card--back" aria-label="Card back">
    <div class="wordmark">Bramwell Lodge</div>
    <div class="divider"></div>
    <div class="contact">
      <div class="person">Dermot Ashby</div>
      <div class="role">Director</div>
      <div class="address">17 Pellham Road<br>Kilbrannan&nbsp;&nbsp;G83 2RN</div>
      <ul>
        <li><svg viewBox="0 0 12 12"><path d="M3 1 L5 3.5 L4 5 Q5.5 7.5 7 8 L8.5 7 L11 9 L9.5 11 Q4 10 1 3 Z"/></svg><span>+971 52 318 6094</span></li>
        <li><svg viewBox="0 0 12 12"><rect x="2" y="5" width="8" height="6" rx="1"/><path d="M1 5 Q6 0 11 5"/></svg><span>+44 7700 900 318</span></li>
        <li><svg viewBox="0 0 12 12"><rect x="1" y="2.5" width="10" height="7"/><path d="M1 2.5 L6 7 L11 2.5"/></svg><span>Dermot.ashby@bramwell.lodge</span></li>
        <li><svg viewBox="0 0 12 12"><circle cx="6" cy="6" r="5"/><ellipse cx="6" cy="6" rx="2.2" ry="5"/><path d="M1 6 H11"/></svg><span>www.<span class="domain">bramwelllodge</span>.com</span></li>
      </ul>
    </div>
  </section>

</main>
</body>
</html>
```